TalkHarbor - Language Coaching Services

Sleek, innovative, trendy design for Language Coaching business.

TalkHarbor is a new UK based company that provides Language Coaching services. We offer highly personalized on-line and face to face language courses. We also impart learning techniques workshops based on the latest neuroscience research for second-language acquisition.

Target Market(s)

See attached info

Industry/Entity Type

Consulting

Contact Information for Business Card

TalkHarbor
DaniaKV@talkharbor.co.uk
TalkHarbor.co.uk
London, UK

Font styles to use
Sans Serif

```html
<!DOCTYPE html>
<html lang="en">
<head>
<meta charset="utf-8">
<title>TalkHarbor Business Card</title>
<link rel="stylesheet" href="https://fonts.googleapis.com/css2?family=Montserrat:wght@300;400;600;700&display=swap">
<style>
  :root {
    --bg: #3f3e3c;
    --blue-deep: #0a5f94;
    --blue-mid: #0d7bbd;
    --blue-glow: #1a9be0;
    --blue-bright: #12a3dd;
    --brand-blue: #0e86c4;
    --ink: #3d3d3d;
    --muted: #777;
    --white: #ffffff;
  }
  * { box-sizing: border-box; margin: 0; padding: 0; }
  html, body { width: 1200px; height: 895px; overflow: hidden; }
  body {
    background: var(--bg);
    font-family: "Montserrat", sans-serif;
    position: relative;
  }
  .card {
    position: absolute;
    top: 289px;
    width: 555px;
    height: 317px;
    border-radius: 22px;
    overflow: hidden;
    box-shadow: 0 10px 24px rgba(0,0,0,.45);
  }

  /* Back side */
  .card-back {
    left: 30px;
    background: radial-gradient(ellipse at 42% 30%, var(--blue-glow) 0%, var(--blue-mid) 40%, var(--blue-deep) 100%);
    color: var(--white);
  }
  .brand {
    display: flex;
    align-items: center;
    gap: 14px;
  }
  .brand-mark {
    border-radius: 50%;
    border-style: solid;
    flex: none;
  }
  .card-back .brand {
    position: absolute;
    top: 70px;
    left: 0; right: 0;
    justify-content: center;
  }
  .card-back .brand-mark { width: 62px; height: 62px; border-width: 6px; border-color: var(--white); }
  .brand-name {
    font-weight: 400;
    font-size: 42px;
    letter-spacing: 1px;
  }
  .card-back .brand-name { color: var(--white); }
  .services-block {
    position: absolute;
    left: 28px;
    right: 28px;
    bottom: 30px;
    display: flex;
    justify-content: space-between;
    align-items: flex-end;
    gap: 18px;
  }
  .services {
    list-style: none;
    font-size: 10px;
    font-weight: 400;
    line-height: 1.55;
    white-space: nowrap;
  }
  .services li::before { content: "•"; margin-right: 7px; }
  .services-right { margin-bottom: 42px; }

  /* Front side */
  .card-front {
    left: 615px;
    background: var(--white);
    color: var(--ink);
  }
  .swoosh { position: absolute; left: 0; bottom: 0; width: 555px; height: 140px; }
  .contact {
    position: absolute;
    left: 34px;
    top: 60px;
    width: 240px;
    text-align: right;
  }
  .person { font-size: 27px; color: var(--blue-bright); font-weight: 700; letter-spacing: .5px; }
  .person .initials { font-weight: 300; color: var(--muted); }
  .role { font-size: 13px; color: var(--ink); margin-top: -2px; }
  .city { font-size: 13px; margin-top: 14px; }
  .details { list-style: none; margin-top: 14px; font-size: 13px; line-height: 1.5; }
  .details li { display: flex; justify-content: flex-end; align-items: center; gap: 7px; }
  .details svg { width: 12px; height: 12px; flex: none; }
  .divider {
    position: absolute;
    left: 290px;
    top: 70px;
    width: 1px;
    height: 130px;
    background: #9a9a9a;
  }
  .card-front .brand { position: absolute; left: 308px; top: 108px; gap: 10px; }
  .card-front .brand-mark { width: 44px; height: 44px; border-width: 5px; border-color: var(--brand-blue); }
  .card-front .brand-name { font-size: 30px; color: var(--brand-blue); }
</style>
</head>
<body>

<section class="card card-back">
  <div class="brand">
    <span class="brand-mark"></span>
    <span class="brand-name">TalkHarbor</span>
  </div>
  <div class="services-block">
    <ul class="services services-left">
      <li>Face to face language coaching session</li>
      <li>On-line language coaching session</li>
      <li>Personalized Newsletters for self-learners</li>
    </ul>
    <ul class="services services-right">
      <li>Language Learning Techniques Workshops</li>
      <li>Mindful Learning Workshops</li>
      <li>Access to premium content, resources</li>
    </ul>
  </div>
</section>

<section class="card card-front">
  <svg class="swoosh" viewBox="0 0 555 140" preserveAspectRatio="none" aria-hidden="true">
    <defs>
      <linearGradient id="swooshFill" x1="0" y1="1" x2="1" y2="0">
        <stop offset="0" stop-color="#1bb3ec"/>
        <stop offset="1" stop-color="#0a5f94"/>
      </linearGradient>
    </defs>
    <path d="M0 140 L0 110 C120 70 260 95 380 70 C460 52 520 20 555 0 L555 140 Z" fill="url(#swooshFill)"/>
    <path d="M0 124 C130 80 270 102 390 78 C470 62 525 30 555 12" fill="none" stroke="#ffffff" stroke-width="3"/>
  </svg>

  <div class="contact">
    <div class="person">DANIA <span class="initials">KV</span></div>
    <div class="role">Director</div>
    <div class="city">London, UK</div>
    <ul class="details">
      <li>020 7946 0318
        <svg viewBox="0 0 12 12"><path d="M3 1 L5 3.5 L4 5 C5 7 6 8 7 8.5 L8.5 7.5 L11 9.5 L9.5 11 C5 11 1 7 1 2.5 Z" fill="#0e86c4"/></svg>
      </li>
      <li>DaniaKV@talkharbor.co.uk
        <svg viewBox="0 0 12 12"><rect x="1" y="2.5" width="10" height="7" fill="#0e86c4"/><path d="M1 2.5 L6 6.5 L11 2.5" fill="none" stroke="#fff" stroke-width="1"/></svg>
      </li>
      <li>www.TalkHarbor.co.uk
        <svg viewBox="0 0 12 12"><circle cx="6" cy="6" r="5" fill="#0e86c4"/><path d="M1 6 H11 M6 1 V11" stroke="#fff" stroke-width=".8"/></svg>
      </li>
    </ul>
  </div>
  <div class="divider"></div>
  <div class="brand">
    <span class="brand-mark"></span>
    <span class="brand-name">TalkHarbor</span>
  </div>
</section>

</body>
</html>
```